Marwick Law Letterhead

We need a new letterhead design for a Law Firm. The address for the law firm is 1475 Calloway Street, Suite 210, Houston, Texas 77041. Phone Number: 832-361-9027; Fax Number: 832-614-7359. The logo is uploaded to the project.

```html
<!DOCTYPE html>
<html lang="en">
<head>
<meta charset="utf-8">
<title>Marwick Law Letterhead</title>
<link href="https://fonts.googleapis.com/css2?family=Montserrat:wght@400;500&display=swap" rel="stylesheet">
<style>
  :root {
    --backdrop: #ececec;
    --paper: #ffffff;
    --navy: #1b2a5c;
    --red: #e8000b;
    --text-grey: #555555;
    --watermark: #f1f2f6;
  }
  * { margin: 0; padding: 0; box-sizing: border-box; }
  html, body {
    width: 1200px;
    height: 1067px;
    overflow: hidden;
    background: var(--backdrop);
    font-family: "Montserrat", sans-serif;
  }
  .letterhead {
    position: absolute;
    left: 200px;
    top: 13px;
    width: 800px;
    height: 1040px;
    background: var(--paper);
  }
  .brand {
    position: absolute;
    left: 60px;
    top: 58px;
    display: flex;
    align-items: center;
    gap: 16px;
  }
  .brand-square {
    width: 48px;
    height: 48px;
    background: var(--navy);
  }
  .brand-name {
    font-size: 30px;
    font-weight: 500;
    color: var(--navy);
    letter-spacing: 0.5px;
  }
  .header-divider {
    position: absolute;
    left: 494px;
    top: 58px;
    width: 1.5px;
    height: 66px;
    background: var(--navy);
  }
  .contact-list {
    position: absolute;
    left: 512px;
    top: 54px;
    list-style: none;
  }
  .contact-item {
    display: flex;
    align-items: center;
    gap: 6px;
    height: 18.6px;
    font-size: 14.5px;
    font-weight: 400;
    color: var(--text-grey);
    letter-spacing: 0.2px;
  }
  .contact-icon {
    width: 10px;
    height: 10px;
    flex: none;
  }
  .watermark {
    position: absolute;
    left: 181px;
    top: 320px;
    width: 437px;
    height: 437px;
    border-radius: 50%;
    background: var(--watermark);
  }
  .address {
    position: absolute;
    left: 0;
    right: 0;
    top: 983px;
    text-align: center;
    font-size: 14.5px;
    color: var(--text-grey);
    letter-spacing: 0.3px;
  }
  .footer-band {
    position: absolute;
    left: 0;
    right: 0;
    bottom: 0;
    height: 15px;
    background: var(--red);
  }
</style>
</head>
<body>
  <main class="letterhead">
    <header>
      <div class="brand">
        <span class="brand-square"></span>
        <span class="brand-name">Marwick Law</span>
      </div>
      <div class="header-divider"></div>
      <ul class="contact-list">
        <li class="contact-item">
          <svg class="contact-icon" viewBox="0 0 10 10"><path d="M2 0.5 L3.6 0.5 L4.2 2.8 L3.1 3.6 Q4 5.9 6.3 7 L7.2 5.9 L9.5 6.5 L9.5 8.2 Q9.3 9.6 7.8 9.5 Q1.2 8.6 0.5 2 Q0.5 0.6 2 0.5 Z" fill="var(--red)"/></svg>
          <span>832-361-9027</span>
        </li>
        <li class="contact-item">
          <svg class="contact-icon" viewBox="0 0 10 10"><rect x="2.5" y="0.5" width="5" height="3" fill="var(--red)"/><rect x="0.5" y="3.5" width="9" height="4" rx="1" fill="var(--red)"/><rect x="2.5" y="6.5" width="5" height="3" fill="var(--red)"/></svg>
          <span>832-614-7359</span>
        </li>
        <li class="contact-item">
          <svg class="contact-icon" viewBox="0 0 10 10"><rect x="0.7" y="2" width="8.6" height="6" fill="none" stroke="var(--red)" stroke-width="1"/><path d="M0.7 2 L5 5.5 L9.3 2" fill="none" stroke="var(--red)" stroke-width="1"/></svg>
          <span>contact@marwicklaw.com</span>
        </li>
        <li class="contact-item">
          <svg class="contact-icon" viewBox="0 0 10 10"><circle cx="5" cy="5" r="4.4" fill="none" stroke="var(--red)" stroke-width="0.9"/><ellipse cx="5" cy="5" rx="2" ry="4.4" fill="none" stroke="var(--red)" stroke-width="0.8"/><path d="M0.6 5 H9.4 M1.3 3 H8.7 M1.3 7 H8.7" stroke="var(--red)" stroke-width="0.7"/></svg>
          <span>www.marwicklaw.com</span>
        </li>
      </ul>
    </header>
    <div class="watermark" role="img" aria-label="Faint brand watermark"></div>
    <footer>
      <p class="address">1475 Calloway Street, Suite 210, Houston, Texas 77041</p>
      <div class="footer-band"></div>
    </footer>
  </main>
</body>
</html>
```